Brookvane Billboard

Please design a billboard using my photos and logos.
For photo of truck please crop the truck itself out and not have the trees / dirt in photo.
Please put " Best Prices in Sevier County"
Please put " 30-yard Dumpsters Starting at 600.00"
Please put " 16-yard Dumpsters Starting at 300.0"
Please put " Delivery and Pickup 7 Days a week"
Billboard size will be 10 ft tall 30 ft wide

```html
<!DOCTYPE html>
<html lang="en">
<head>
<meta charset="utf-8">
<title>Brookvane Dumpsters Billboard</title>
<link href="https://fonts.googleapis.com/css2?family=Poppins:wght@700;800&display=swap" rel="stylesheet">
<style>
  :root {
    --ink: #070707;
    --violet: #7b3a98;
    --paper: #ffffff;
    --stage: #ececec;
    --truck-light: #e9eaec;
    --truck-mid: #b9bcc2;
    --truck-dark: #3a2b5e;
  }
  html, body {
    margin: 0;
    width: 911px;
    height: 1200px;
    overflow: hidden;
    background: var(--stage);
  }
  .billboard {
    position: absolute;
    left: 30px;
    top: 458px;
    width: 851px;
    height: 283px;
    box-shadow: 0 10px 24px rgba(0,0,0,.18);
  }
  .billboard svg { display: block; width: 100%; height: 100%; }
  .brand-name,
  .headline,
  .offer {
    font-family: "Poppins", sans-serif;
    fill: var(--paper);
  }
  .brand-name { font-weight: 800; }
  .headline { font-weight: 800; }
  .offer { font-weight: 700; }
  .chevron { fill: none; stroke: var(--paper); stroke-width: 4; stroke-linejoin: miter; }
</style>
</head>
<body>
  <div class="billboard">
    <svg viewBox="0 0 1458 485" xmlns="http://www.w3.org/2000/svg">
      <defs>
        <linearGradient id="truck-tones" x1="0" y1="0" x2="1" y2="0">
          <stop offset="0" stop-color="var(--truck-light)"/>
          <stop offset="0.55" stop-color="var(--truck-mid)"/>
          <stop offset="1" stop-color="var(--truck-dark)"/>
        </linearGradient>
        <clipPath id="board-clip"><rect width="1458" height="485"/></clipPath>
      </defs>

      <g clip-path="url(#board-clip)">
        <rect class="board-base" width="1458" height="485" fill="var(--ink)"/>
        <ellipse class="accent-ring" cx="1240" cy="190" rx="560" ry="290" fill="var(--violet)"/>
        <ellipse class="photo-field" cx="1240" cy="190" rx="520" ry="260" fill="var(--paper)"/>
        <rect class="headline-band" x="0" y="186" width="800" height="162" fill="var(--violet)"/>

        <rect class="truck-photo" x="770" y="30" width="688" height="440" rx="30"
              fill="url(#truck-tones)" opacity="0.85"
              role="img" aria-label="Photo of a white roll-off truck carrying a purple 30-yard dumpster"/>
      </g>

      <g class="brand">
        <text class="brand-name" x="98" y="108" font-size="80" textLength="455" lengthAdjust="spacingAndGlyphs">BROOKVANE</text>
        <text class="brand-name" x="553" y="162" font-size="44" text-anchor="end">DUMPSTERS</text>
      </g>

      <g class="headline-block">
        <text class="headline" x="30" y="250" font-size="70" textLength="540" lengthAdjust="spacingAndGlyphs">BEST PRICES IN</text>
        <text class="headline" x="24" y="334" font-size="98" textLength="742" lengthAdjust="spacingAndGlyphs">SEVIER COUNTY</text>
      </g>

      <g class="offer-list">
        <g class="offer-item">
          <path class="chevron" d="M36 364 l8 8 -8 8 M46 364 l8 8 -8 8"/>
          <text class="offer" x="66" y="383" font-size="28">30-YARD DUMPSTERS STARTING AT 600.00</text>
        </g>
        <g class="offer-item">
          <path class="chevron" d="M36 405 l8 8 -8 8 M46 405 l8 8 -8 8"/>
          <text class="offer" x="66" y="424" font-size="28">16-YARD DUMPSTERS STARTING AT 300.0</text>
        </g>
        <g class="offer-item">
          <path class="chevron" d="M36 446 l8 8 -8 8 M46 446 l8 8 -8 8"/>
          <text class="offer" x="66" y="465" font-size="28">DELIVERY AND PICKUP 7 DAYS A WEEK</text>
        </g>
      </g>
    </svg>
  </div>
</body>
</html>
```